Brochure design for International Beauty Trade Show

I neee a tri-fold company products' brochure to distribute to customers at an international trade show coming soon. We have 4 main product categories- hair and skincare, facial care, Body and bath and massage oil.
The brochure needs to include at least 2 photos of the main products of each category, benefits, call to action and our company contact info ( website and phone number).

Target Market(s)

Educated and high income earners looking for all-natural,pure, 100 organic products for their beauty and personal care needs. Our products cross all racial groups/demographics and suitable for all skin types

Industry/Entity Type

Hair And Beauty

Font styles to use
Serif

Colors

Designer to choose colors to be used in the design.

Requirements
Must have
• The design must stand out as pure and luxury and at the same time be inclusive using our logo design colors- orange and blue. Also, the content must be easy to read and captivating.
• Finally if using women pictures, please include Black, white, Asian and Latina to reflect the fact that our products are suitable for all skin types.
Nice to have
• Design the brochure such that it could be printed as a poster-banner ad.
Should not have
• Cookie cutter designs are not welcome

```html
<!DOCTYPE html>
<html lang="en">
<head>
<meta charset="utf-8">
<title>Verdalis Naturals – Tri-fold Brochure</title>
<link rel="stylesheet" href="https://fonts.googleapis.com/css2?family=Montserrat:wght@400;600;700&display=swap">
<style>
  :root {
    --orange: #f07a1a;
    --blue: #1e9be0;
    --green-dark: #2f7a18;
    --green: #5cae28;
    --green-light: #a8d85a;
    --ink: #2a2a2a;
    --paper: #ffffff;
    --stage: #e4e4e4;
    --photo-warm: #c99a7c;
  }
  * { box-sizing: border-box; margin: 0; padding: 0; }
  html, body { width: 1200px; height: 1000px; overflow: hidden; }
  body {
    background: var(--stage);
    font-family: "Montserrat", sans-serif;
    color: var(--ink);
    position: relative;
  }
  .sheet {
    position: absolute;
    left: 50px;
    width: 1100px;
    height: 450px;
    background: var(--paper);
    box-shadow: 0 4px 14px rgba(0,0,0,.15);
    overflow: hidden;
  }
  .sheet--outer { top: 30px; }
  .sheet--inner { top: 520px; }
  .sheet__art { position: absolute; inset: 0; }
  .fold {
    position: absolute; top: 0; bottom: 0; width: 1px;
    background: rgba(0,0,0,.07);
  }
  .panel { position: absolute; top: 0; bottom: 0; width: 366px; }
  .panel--1 { left: 0; }
  .panel--2 { left: 367px; }
  .panel--3 { left: 734px; }

  .heading {
    font-weight: 400;
    font-size: 28px;
    line-height: 1.05;
    position: absolute;
  }
  .heading--orange { color: var(--orange); }
  .heading--blue { color: var(--blue); }

  .benefits { position: absolute; list-style: none; font-size: 12.5px; line-height: 1.7; }
  .benefits li { display: flex; align-items: center; gap: 8px; }
  .tick { width: 13px; height: 13px; flex: none; }
  .tick--orange { color: var(--orange); }
  .tick--blue { color: var(--blue); }

  .about {
    position: absolute; top: 22px; left: 40px; width: 290px;
    color: #fff; text-align: center; font-size: 12.5px; line-height: 1.45;
    text-shadow: 0 1px 2px rgba(0,0,0,.35);
  }
  .about__title { font-weight: 700; font-size: 17px; margin-bottom: 6px; }

  .tagline {
    position: absolute; top: 40px; right: 30px; text-align: right;
    color: #fff; font-size: 24px; line-height: 1.2;
    text-shadow: 0 1px 3px rgba(0,0,0,.35);
  }
  .tagline strong { font-weight: 700; }

  .contact {
    position: absolute; top: 300px; left: 0; width: 366px;
    text-align: center; font-weight: 700; font-size: 15px; line-height: 1.6;
  }
  .brand-dot {
    position: absolute; top: 225px; left: 155px;
    width: 56px; height: 56px; border-radius: 50%; background: var(--orange);
  }
  .brand {
    position: absolute; top: 330px; left: 0; width: 366px;
    display: flex; align-items: center; justify-content: center; gap: 10px;
    color: var(--orange); font-weight: 600; font-size: 30px; letter-spacing: 1px;
  }
  .brand__dot { width: 26px; height: 26px; border-radius: 50%; background: var(--orange); }
  .web {
    position: absolute; bottom: 22px; left: 0; width: 366px; text-align: center;
    color: var(--blue); font-weight: 700; font-size: 14px;
  }
  .product {
    position: absolute; border-radius: 6px;
  }
</style>
</head>
<body>
<svg width="0" height="0" style="position:absolute">
  <symbol id="tick" viewBox="0 0 14 14">
    <rect x="1" y="1" width="12" height="12" fill="none" stroke="currentColor" stroke-width="1.5"/>
    <path d="M3.5 7.2 L6 9.8 L11 3.5" fill="none" stroke="currentColor" stroke-width="2"/>
  </symbol>
  <linearGradient id="greenPhoto" x1="0" y1="0" x2="1" y2="1">
    <stop offset="0" stop-color="#7cc63a"/>
    <stop offset=".55" stop-color="#3f8f1e"/>
    <stop offset="1" stop-color="#1f4f12"/>
  </linearGradient>
  <linearGradient id="bottlePhoto" x1="0" y1="0" x2="0" y2="1">
    <stop offset="0" stop-color="#e6efe0"/>
    <stop offset="1" stop-color="#c98a4a"/>
  </linearGradient>
  <linearGradient id="portraitPhoto" x1="0" y1="0" x2="1" y2="0">
    <stop offset="0" stop-color="#6a4a3a"/>
    <stop offset="1" stop-color="#c99a7c"/>
  </linearGradient>
</svg>

<!-- Outer side: back, contact, cover -->
<section class="sheet sheet--outer">
  <svg class="sheet__art" viewBox="0 0 1100 450" width="1100" height="450">
    <rect role="img" aria-label="Hair and skincare product bottles" x="40" y="15" width="260" height="135" rx="8" fill="url(#bottlePhoto)" opacity=".8"/>
    <path role="img" aria-label="Green spa scene with orchid, bamboo and stones, model with long hair"
          d="M367 0 H1100 V300 C1000,340 920,280 840,265 C720,245 620,290 520,250 C450,222 410,180 367,170 Z"
          fill="url(#greenPhoto)"/>
    <path role="img" aria-label="Portrait of a smiling woman" d="M850 140 h200 v150 c-60,20 -130,0 -200,-25 Z" fill="url(#portraitPhoto)" opacity=".85"/>
    <path d="M0 170 C120,160 250,150 367,170 C410,180 450,222 520,250 C620,290 720,245 840,265 C920,280 1000,340 1100,300"
          fill="none" stroke="var(--orange)" stroke-width="12"/>
    <path d="M0 182 C120,172 250,162 367,182 C410,192 450,234 520,262 C620,302 720,257 840,277 C920,292 1000,352 1100,312"
          fill="none" stroke="var(--blue)" stroke-width="4"/>
  </svg>
  <div class="fold" style="left:366px"></div>
  <div class="fold" style="left:733px"></div>

  <div class="panel panel--1">
    <h2 class="heading heading--orange" style="top:210px;left:40px">Hair &amp;<br>Skincare</h2>
    <ul class="benefits" style="top:280px;left:40px">
      <li><svg class="tick tick--orange"><use href="#tick"/></svg>Natural moisturizer</li>
      <li><svg class="tick tick--orange"><use href="#tick"/></svg>Heal damaged hair or sensitive scalp</li>
      <li><svg class="tick tick--orange"><use href="#tick"/></svg>Soften curly and frizzy hair</li>
      <li><svg class="tick tick--orange"><use href="#tick"/></svg>Antiaging, remove wrinkles</li>
      <li><svg class="tick tick--orange"><use href="#tick"/></svg>Reduce sebum secretion</li>
      <li><svg class="tick tick--orange"><use href="#tick"/></svg>Tone, sooth and restore luster</li>
      <li><svg class="tick tick--orange"><use href="#tick"/></svg>Restore fair complexion</li>
    </ul>
  </div>

  <div class="panel panel--2">
    <div class="about">
      <p class="about__title">ABOUT US:</p>
      <p>Verdalis Naturals is an export/import company. Our mission is to satisfy our customers by supplying them with pure, 100% organic products, that make them more attractive and solve the most common skin and hair problems.</p>
    </div>
    <div class="brand-dot"></div>
    <p class="contact">(800) 555-0147<br>hello@verdalis.com<br>www.verdalis.com</p>
  </div>

  <div class="panel panel--3">
    <p class="tagline"><strong>Natural Solutions</strong><br>to Forever Beauty</p>
    <div class="brand"><span class="brand__dot"></span>VERDALIS</div>
    <p class="web">www.verdalis.com</p>
  </div>
</section>

<!-- Inner side: three product categories -->
<section class="sheet sheet--inner">
  <svg class="sheet__art" viewBox="0 0 1100 450" width="1100" height="450">
    <path role="img" aria-label="Bamboo and spa stones with orchid and candle, model applying cream"
          d="M0 0 H1100 V95 C960,90 820,95 733,110 C600,135 480,185 366,180 C250,176 120,165 0,160 Z"
          fill="url(#greenPhoto)"/>
    <path role="img" aria-label="Woman holding a jar of cream" d="M60 10 h230 v165 c-80,5 -160,-5 -230,-12 Z" fill="url(#portraitPhoto)" opacity=".85"/>
    <path d="M0 160 C120,165 250,176 366,180 C480,185 600,135 733,110 C820,95 960,90 1100,95"
          fill="none" stroke="var(--orange)" stroke-width="10"/>
    <path d="M0 172 C120,177 250,188 366,192 C480,197 600,147 733,122 C820,107 960,102 1100,107"
          fill="none" stroke="var(--blue)" stroke-width="4"/>
  </svg>
  <div class="fold" style="left:366px"></div>
  <div class="fold" style="left:733px"></div>

  <div class="panel panel--1">
    <h2 class="heading heading--orange" style="top:205px;left:40px">Facial Care</h2>
    <ul class="benefits" style="top:245px;left:40px">
      <li><svg class="tick tick--orange"><use href="#tick"/></svg>Reduce sebum secretion</li>
      <li><svg class="tick tick--orange"><use href="#tick"/></svg>Eliminate toxins &amp; blemishes</li>
      <li><svg class="tick tick--orange"><use href="#tick"/></svg>Tighten pores</li>
      <li><svg class="tick tick--orange"><use href="#tick"/></svg>Dries pimples</li>
      <li><svg class="tick tick--orange"><use href="#tick"/></svg>Remove blackheads</li>
    </ul>
    <div class="product" role="img" aria-label="Face cream jar and facial soap box" style="left:70px;top:355px;width:230px;height:75px;background:linear-gradient(90deg,#ece6d6,#8dbf6a)"></div>
  </div>

  <div class="panel panel--2">
    <div class="product" role="img" aria-label="Body soap boxes with lemon and prickly pear fruit" style="left:50px;top:185px;width:250px;height:80px;background:linear-gradient(90deg,#f2d548,#6fb34a,#c9405a)"></div>
    <h2 class="heading heading--blue" style="top:280px;left:45px">Body &amp;<br>Bath Care</h2>
    <ul class="benefits" style="top:345px;left:45px">
      <li><svg class="tick tick--blue"><use href="#tick"/></svg>Purify and disinfect</li>
      <li><svg class="tick tick--blue"><use href="#tick"/></svg>Fight acne</li>
      <li><svg class="tick tick--blue"><use href="#tick"/></svg>Rejuvenate &amp; hydrate</li>
      <li><svg class="tick tick--blue"><use href="#tick"/></svg>Promote healthy looking skin</li>
      <li><svg class="tick tick--blue"><use href="#tick"/></svg>Remove dead cells</li>
    </ul>
  </div>

  <div class="panel panel--3">
    <h2 class="heading heading--orange" style="top:125px;left:40px">Massage<br>Care</h2>
    <ul class="benefits" style="top:190px;left:40px">
      <li><svg class="tick tick--blue"><use href="#tick"/></svg>Relief stress and pain</li>
      <li><svg class="tick tick--blue"><use href="#tick"/></svg>Fight muscle contraction/tenderness</li>
      <li><svg class="tick tick--blue"><use href="#tick"/></svg>Eliminate stretch marks</li>
      <li><svg class="tick tick--blue"><use href="#tick"/></svg>Pure, undiluted</li>
    </ul>
    <div class="product" role="img" aria-label="Massage oil spray bottle with red berries" style="left:190px;top:280px;width:130px;height:150px;background:linear-gradient(180deg,#3a3560,#b8263a)"></div>
  </div>
</section>
</body>
</html>
```